Window company.

Hello,

We are a small family business located in Madrid, Spain that works nationwide to fix, change or mount the windows of your home / premises.

The group of possible clients to whom the flyer is focused ranges from 30 to 65 years, families in general who want comfort at home and extra savings every year in heating.

It must include not only graphics and a striking aesthetic in accordance with the concepts of wanting to reach / transmit the final product to the customer to sell the product.

Details to also include:

-Brief history of the company and its foundation in 2006. It will be subsequently translated into Spanish so put in words what you consider necessary so that the client stays with the concept that we are professionals.

--Specialized in exterior aluminum and PVC carpentry.

-We move to your home for a first visit and we provide the budget totally free without any commitment.

- Also payment facilities; up to 3 times, without interest.

-Contact details of the company. (WhatsApp, email, phone and location)
Open: Mon - Friday 11,00am - 9pm
Saturday: 12,00am - 7pm
Sunday: Closed

Also as a suggestion, to decide on your own, graphics of types of window openings, if you consider that anything that is striking for the client so it wonr be yet another advertising flyer.

We are open to all kinds of ideas, all of them involving marketing branding.

We are open to any type of idea and we want to stand out, the construction world is tough and we have an idea to grow, taking into account that it must not only be beautiful but commercial to attract potential customers with all kinds of purchasing power.

Thank you.

```html
<!DOCTYPE html>
<html lang="en">
<head>
<meta charset="utf-8">
<title>Vantora – Window Flyer</title>
<link href="https://fonts.googleapis.com/css2?family=Oswald:wght@500&family=Source+Sans+3:wght@400;600;700&display=swap" rel="stylesheet">
<style>
:root{
  --red:#c8332a;
  --ink:#3a3a3a;
  --grey:#6b6b6b;
  --mid-grey:#8a8a8a;
  --pale:#f2f2f2;
  --page:#4a4646;
  --white:#ffffff;
}
*{margin:0;padding:0;box-sizing:border-box}
html,body{width:1200px;height:800px;overflow:hidden;background:var(--page)}
.flyer{
  position:absolute;left:320px;top:4px;width:595px;height:843px;
  transform:scale(.94);transform-origin:0 0;
  background:var(--white);overflow:hidden;
  font-family:"Source Sans 3",sans-serif;color:var(--ink);
}
.abs{position:absolute}
.brand-name{left:112px;top:58px;font-size:27px;font-weight:600;letter-spacing:1px;color:var(--mid-grey)}
.brand-mark{left:26px;top:50px;width:74px;height:46px;border:3px solid var(--red)}
.socials{right:22px;top:27px;display:flex;gap:18px}
.socials span{width:26px;height:26px;border:1.5px solid #a9a9a9;border-radius:50%;display:block}
.hero-photo{
  left:0;top:0;width:595px;height:368px;
  clip-path:polygon(260px 118px,295px 70px,595px 70px,595px 368px,0 368px,0 118px);
  background:linear-gradient(90deg,#ffffff 0%,#f4f4f4 22%,#c9c6c3 45%,#9d948c 65%,#6f6a66 85%,#4d4a48 100%);
}
.hero-line{left:0;top:0}
.headline{left:24px;top:136px;font-family:"Oswald",sans-serif;font-weight:500;font-size:32px;line-height:36px;color:var(--ink)}
.offer-band{
  left:0;top:252px;width:295px;height:42px;background:var(--red);
  clip-path:polygon(0 0,280px 0,295px 42px,0 42px);
  font-family:"Oswald",sans-serif;font-size:22px;color:var(--white);
  padding:4px 0 0 24px;letter-spacing:-.3px;
}
.quality{left:25px;top:302px;font-family:"Oswald",sans-serif;font-size:20px;color:var(--ink);letter-spacing:-.3px}
.about{left:0;top:368px;width:595px;height:166px;background:linear-gradient(180deg,#f6f6f6,#ffffff)}
.section-title{font-size:16px;font-weight:700;color:var(--red)}
.about-title{left:24px;top:390px}
.about-text{left:24px;top:420px;width:254px;font-size:12.5px;line-height:16px;text-align:justify}
.divider{left:296px;top:384px;width:1px;height:118px;background:#c8c8c8}
.spec-title{left:311px;top:392px;font-size:11.5px;font-weight:700;line-height:14px}
.spec-text{left:312px;top:429px;width:272px;font-size:12px;line-height:16px;letter-spacing:-.3px}
.pay-button{left:313px;top:468px;width:272px;height:25px;background:var(--red);color:var(--white);font-size:10px;font-weight:700;text-align:center;line-height:25px;letter-spacing:-.2px}
.services{
  left:0;top:535px;width:595px;height:172px;
  border-top:3px solid var(--red);border-bottom:3px solid var(--red);
  background:linear-gradient(180deg,#6e6e6e 0%,#7c7c7c 45%,#5f5f5f 100%);
}
.services-tab{left:0;top:518px;width:195px;height:28px;background:var(--red);clip-path:polygon(0 0,195px 0,180px 28px,0 28px);color:var(--white);font-size:16px;font-weight:700;padding:3px 0 0 24px}
.service-list{list-style:none;left:30px;top:555px;display:grid;grid-template-columns:268px 250px;row-gap:6px}
.service{display:flex;align-items:center;gap:13px;color:var(--white);font-size:14.5px;font-weight:600;height:30px}
.service-icon{width:31px;height:30px;border:1.5px solid #d6d6d6;border-radius:3px;background:#f4f4f4;display:flex;align-items:center;justify-content:center}
.service-icon i{display:block;width:16px;height:16px;border:2px solid var(--red)}
.hours{left:0;top:730px;width:595px;text-align:center;font-size:12.5px;color:#222}
.footer{left:0;top:783px;width:595px;height:60px;background:var(--red)}
.call-pill{left:55px;top:768px;width:478px;height:29px;border-radius:15px;background:#8e8e8e;color:var(--white);font-size:13px;font-weight:600;text-align:center;line-height:29px}
.call-pill b{font-size:15px;font-weight:700}
.call-pill svg{vertical-align:-2px;margin-right:4px}
.contact{left:0;top:802px;width:595px;text-align:center;color:var(--white);font-size:13px;line-height:17px}
</style>
</head>
<body>
<div class="flyer">
  <div class="abs hero-photo" role="img" aria-label="Photo of a smiling family of four sitting on a rug in a bright living room"></div>
  <svg class="abs hero-line" width="595" height="130" viewBox="0 0 595 130"><polyline points="0,118 260,118 295,70 595,70" fill="none" stroke="#c8332a" stroke-width="3"/></svg>

  <div class="abs brand-mark"></div>
  <div class="abs brand-name">VANTORA</div>
  <div class="abs socials"><span></span><span></span><span></span><span></span></div>

  <h1 class="abs headline">SAVINGS<br>EVERY YEAR<br>IN HEATING</h1>
  <div class="abs offer-band">Budgets with no obligation.</div>
  <div class="abs quality">QUALITY GUARANTEED!</div>

  <div class="abs about"></div>
  <h2 class="abs section-title about-title">WHO WE ARE</h2>
  <p class="abs about-text">We are a small family business located in Madrid, Spain that works nationwide to fix, change or mount the windows of your home / premises founded 2006.</p>
  <div class="abs divider"></div>
  <h3 class="abs spec-title">SPECIALIZED IN EXTERIOR ALUMINUM<br>AND PVC CARPENTRY.</h3>
  <p class="abs spec-text">We move to your home for a first visit and we provide the budget totally free without any commitment.</p>
  <div class="abs pay-button">PAYMENT FACILITIES; UP TO 3 TIMES, WITHOUT INTEREST</div>

  <div class="abs services" role="img" aria-label="Greyscale photo of a suburban family house"></div>
  <h2 class="abs services-tab">OUR SERVICES</h2>
  <ul class="abs service-list">
    <li class="service"><span class="service-icon"><i></i></span>OUTDOOR CARPENTRY</li>
    <li class="service"><span class="service-icon"><i></i></span>PVC</li>
    <li class="service"><span class="service-icon"><i></i></span>TOLDOS</li>
    <li class="service"><span class="service-icon"><i></i></span>MOSQUITO NETS</li>
    <li class="service"><span class="service-icon"><i></i></span>ALUMINUM</li>
    <li class="service"><span class="service-icon"><i></i></span>LUCERNARIOS</li>
    <li class="service"><span class="service-icon"><i></i></span>GLAZING</li>
    <li class="service"><span class="service-icon"><i></i></span>AND MUCH MORE</li>
  </ul>

  <p class="abs hours">OPEN: MON - FRIDAY 11,00AM - 9PM &nbsp;|&nbsp; SATURDAY: 12,00AM - 7PM &nbsp;|&nbsp; SUNDAY: CLOSED</p>

  <div class="abs footer"></div>
  <div class="abs call-pill">Call Vantora on
    <svg width="13" height="13" viewBox="0 0 24 24"><path d="M6.6 10.8a15 15 0 006.6 6.6l2.2-2.2c.3-.3.7-.4 1-.2 1.1.4 2.3.6 3.6.6.6 0 1 .4 1 1V20c0 .6-.4 1-1 1A17 17 0 013 4c0-.6.4-1 1-1h3.5c.6 0 1 .4 1 1 0 1.3.2 2.5.6 3.6.1.3 0 .7-.2 1z" fill="#fff"/></svg><b>+34 611 42 57 90</b> for more information</div>
  <p class="abs contact">hello@vantorawindows.com | www.vantorawindows.com<br>Pol. Ind. Las Acacias 14, Getafe, Spain 28906</p>
</div>
</body>
</html>
```